Audit/Compliance company needs Business Card Template

We are after a Business Card Template that we can modify internally to update details as people change positions.
We are an Australian based company specalising in Auditing and Quality/OHS systems development. - See www.brimfieldreview.com.au for more information
We would like the desings to be based around our logo and colours assocaited with it (attached for your information) however we are very open as to how the cards are designed.
We are looking for something quite edgy and mordern but it must have a professional/compliance feel to it (if possible).
The main details we would like to include within the card template are:
Name
Position Title
Postal Address
Phone Number
Mobile Number
Email Address
Website
The cards will be printed through lanterly press on Glossy paper so it should reflect the requirements below
Full Bleed Size (starting document size)
90 x 52 mm
1062 x 615 pixels
Document Trim Size (final size after being cut)
87 x 49 mm
1028 x 579 pixels
Resolution
300 DPI

```html
<!DOCTYPE html>
<html lang="en">
<head>
<meta charset="utf-8">
<title>Brimfield Review – Business Card</title>
<link rel="stylesheet" href="https://fonts.googleapis.com/css2?family=Open+Sans:wght@400&display=swap">
<style>
  :root {
    --page: #ffffff;
    --charcoal: #434043;
    --orange: #f08731;
    --ink: #4a4242;
    --rule: #5a4a40;
  }
  * { margin: 0; padding: 0; box-sizing: border-box; }
  html, body {
    width: 912px; height: 1200px; overflow: hidden;
    background: var(--page);
    font-family: "Open Sans", Arial, sans-serif;
  }
  .canvas { position: relative; width: 912px; height: 1200px; }

  .card { position: absolute; left: 30px; width: 862px; height: 497px; }
  .card-front { top: 89px; background: var(--charcoal); }
  .card-back { top: 628px; background: var(--orange); color: var(--ink); }

  .brand {
    position: absolute; left: 68px; top: 213px;
    display: flex; align-items: center; gap: 14px;
  }
  .brand-mark { width: 64px; height: 64px; border-radius: 50%; background: var(--orange); }
  .brand-rule { width: 1px; height: 62px; background: var(--orange); }
  .brand-name { color: var(--orange); font-size: 25px; letter-spacing: 0.5px; }

  .front-divider {
    position: absolute; left: 532px; top: 144px;
    width: 1px; height: 208px; background: var(--orange);
  }
  .person { position: absolute; left: 593px; top: 214px; width: 200px; text-align: center; color: var(--orange); }
  .person-name { font-size: 27px; line-height: 1.2; }
  .person-title { font-size: 20px; margin-top: 14px; }

  .phone, .mobile { position: absolute; top: 13px; font-size: 23px; }
  .phone { left: 12px; }
  .mobile { right: 14px; }

  .details { position: absolute; left: 0; right: 0; top: 142px; text-align: center; font-size: 23px; }
  .detail-line { line-height: 34px; }
  .detail-rule { width: 536px; height: 1px; margin: 23px auto 24px; background: var(--rule); opacity: 0.8; }
</style>
</head>
<body>
<div class="canvas">
  <section class="card card-front">
    <div class="brand">
      <span class="brand-mark"></span>
      <span class="brand-rule"></span>
      <span class="brand-name">Brimfield Review</span>
    </div>
    <div class="front-divider"></div>
    <div class="person">
      <p class="person-name">Darel Voskin</p>
      <p class="person-title">Manager</p>
    </div>
  </section>

  <section class="card card-back">
    <p class="phone">Phone number</p>
    <p class="mobile">Mobile number</p>
    <div class="details">
      <p class="detail-line">email@email.com</p>
      <div class="detail-rule"></div>
      <p class="detail-line">www.brimfieldreview.com.au</p>
      <div class="detail-rule"></div>
      <p class="detail-line">House no. 48, Fenwick Row, Sydney, Australia</p>
    </div>
  </section>
</div>
</body>
</html>
```